I would like a business card to match my truck wrap and logo. I would like the font to match my existing business card please.

Industry/Entity Type

Painter

Contact Information for Business Card

Rodrigo Fenwar 801-437-2190 Fenwarcoatings.utah@brelmox.com
SERVICES - Custom Paint & Stain, Interior & Exterior, Epoxy Coatings / Garage Floors, Cabinet Refinishing, Log Staining and Refinishing.

Requirements
Nice to have
• I would like to have the white and grey line like the bottom of my vehicle wrap, Light Grey to match my truck also.

```html
<!DOCTYPE html>
<html lang="en">
<head>
<meta charset="utf-8">
<title>Fenwar Coatings – Business Card</title>
<link rel="stylesheet" href="https://fonts.googleapis.com/css2?family=Arimo:wght@400;700&family=Russo+One&display=swap">
<style>
  :root {
    --stage: #000000;
    --card: #353537;
    --card-stripe: rgba(255,255,255,0.018);
    --white: #ffffff;
    --soft-white: #e6e6e6;
    --rule: #6a6a6c;
    --blue: #1e9be0;
  }
  * { margin: 0; padding: 0; box-sizing: border-box; }
  html, body {
    width: 1200px; height: 900px; overflow: hidden;
    background: var(--stage);
    font-family: "Arimo", Arial, sans-serif;
  }
  .card {
    position: absolute;
    width: 458px; height: 282px;
    border-radius: 14px;
    overflow: hidden;
    background-color: var(--card);
    background-image: repeating-linear-gradient(90deg, var(--card-stripe) 0 1px, transparent 1px 3px);
    color: var(--white);
  }
  .card--front { left: 138px; top: 265px; }
  .card--back  { left: 625px; top: 268px; }

  /* Front */
  .brand-stack {
    position: absolute; left: 22px; top: 74px; width: 148px;
    display: flex; flex-direction: column; align-items: center;
    font-weight: 700; color: var(--white);
  }
  .brand-mark {
    width: 34px; height: 34px; background: var(--white); margin-bottom: 14px;
  }
  .brand-name { font-size: 30px; line-height: 1; letter-spacing: 1px; }
  .brand-sub { font-size: 11px; letter-spacing: 5.4px; margin-top: 5px; margin-right: -5.4px; }
  .divider {
    position: absolute; left: 196px; top: 89px; width: 1px; height: 102px;
    background: var(--rule);
  }
  .person {
    position: absolute; left: 216px; top: 101px;
    font-family: "Russo One", sans-serif; font-size: 18px; letter-spacing: 0.3px;
    white-space: nowrap;
  }
  .contact {
    position: absolute; left: 216px; top: 145px;
    font-size: 12.5px; color: var(--soft-white); white-space: nowrap;
  }
  .contact li { list-style: none; display: flex; align-items: center; gap: 5px; height: 17px; }
  .contact svg { width: 12px; height: 12px; flex: none; }

  /* Back */
  .brand-row {
    position: absolute; left: 0; right: 0; top: 60px;
    display: flex; justify-content: center; align-items: center; gap: 14px;
    color: var(--blue); font-weight: 700;
  }
  .brand-row .brand-mark { background: var(--blue); width: 40px; height: 40px; margin: 0; }
  .brand-row .brand-text { display: flex; flex-direction: column; }
  .brand-row .brand-name { font-size: 30px; }
  .brand-row .brand-sub { font-size: 11px; letter-spacing: 6.6px; margin-top: 4px; }
  .services-title {
    position: absolute; left: 0; right: 0; top: 154px;
    display: flex; justify-content: center; align-items: center; gap: 12px;
    font-size: 15.5px; font-weight: 700;
  }
  .services-title::before, .services-title::after {
    content: ""; width: 72px; height: 1px; background: var(--rule);
  }
  .services-list {
    position: absolute; left: 0; right: 0; top: 179px;
    text-align: center; font-size: 13.8px; line-height: 16.5px; color: var(--soft-white);
  }
  .dot {
    display: inline-block; width: 6px; height: 6px; border-radius: 50%;
    background: var(--blue); margin: 0 6px 2px 3px; vertical-align: middle;
  }
</style>
</head>
<body>
  <section class="card card--front">
    <div class="brand-stack">
      <span class="brand-mark"></span>
      <span class="brand-name">FENWAR</span>
      <span class="brand-sub">COATINGS</span>
    </div>
    <span class="divider"></span>
    <h1 class="person">RODRIGO FENWAR</h1>
    <ul class="contact">
      <li>
        <svg viewBox="0 0 24 24" aria-hidden="true"><path fill="#fff" d="M6.6 10.8a15.1 15.1 0 0 0 6.6 6.6l2.2-2.2a1 1 0 0 1 1-.25 11.4 11.4 0 0 0 3.6.57 1 1 0 0 1 1 1V20a1 1 0 0 1-1 1A17 17 0 0 1 3 4a1 1 0 0 1 1-1h3.5a1 1 0 0 1 1 1c0 1.250.2 2.450.57 3.57a1 1 0 0 1-.25 1z"/></svg>
        801-437-2190
      </li>
      <li>
        <svg viewBox="0 0 24 24" aria-hidden="true"><path fill="#fff" d="M2 5h20v14H2z"/><path fill="none" stroke="#353537" stroke-width="1.6" d="M2 5l10 8 10-8M2 19l7-7M22 19l-7-7"/></svg>
        Fenwarcoatings.utah@brelmox.com
      </li>
    </ul>
  </section>

  <section class="card card--back">
    <div class="brand-row">
      <span class="brand-mark"></span>
      <div class="brand-text">
        <span class="brand-name">FENWAR</span>
        <span class="brand-sub">COATINGS</span>
      </div>
    </div>
    <h2 class="services-title">SERVICES</h2>
    <p class="services-list">
      Custom Paint &amp; Stain<span class="dot"></span>Interior &amp; Exterior<br>
      Epoxy Coatings / Garage Floors <span class="dot"></span> Cabinet Refinishing<br>
      Log Staining and Refinishing.
    </p>
  </section>
</body>
</html>
```